Custom Software Solutions

web design for a small custom programming company in Brisbane Australia. Specialize in business finance solutions, Office Suite automation and programming and data analysis. The design should portray professionalism and honesty. Main applications deal with financial accounting reporting and analysis. Would like to see colors blue and purple used (but sparsely). added file is company logo. Trading name is TR Solutions, while the official company name is TR Solutions (QLD) Pty Ltd.

Target Market(s)

current clients for support
marketing tool for prospective clients

Industry/Entity Type

Business

Number of Pages Required

5+ page

Font styles to use
Sans Serif

Colors
0555a3
a54599
ffffff

Requirements
Must have
• introduction
• blog for news and tips
• previous and current clients/projects page
• contact us page with email submission form
Should not have
• social media links

```html
<!DOCTYPE html>
<html lang="en">
<head>
<meta charset="utf-8">
<title>TR Solutions</title>
<link href="https://fonts.googleapis.com/css2?family=Mulish:wght@300;400;600&display=swap" rel="stylesheet">
<style>
:root{
  --blue:#0555a3;
  --navy:#0b4c87;
  --purple:#a54599;
  --ink:#1d3f6e;
  --text:#555b63;
  --rule:#e4e6ea;
  --card:#f7f7f8;
  --white:#ffffff;
}
*{box-sizing:border-box;margin:0;padding:0}
html,body{width:848px;height:1200px;overflow:hidden;background:var(--white)}
body{position:relative;font-family:'Mulish',Arial,sans-serif;color:var(--text);font-weight:300}
.abs{position:absolute}
a{color:var(--blue);text-decoration:none}

.brand{left:56px;top:40px}
.brand-name{font-size:18px;font-weight:400;color:var(--blue);letter-spacing:1.5px}

.contact{right:52px;top:18px;text-align:right;line-height:1.55}
.contact .label{color:var(--purple);font-size:13px;font-weight:400}
.contact .phone{color:var(--ink);font-size:13px;font-weight:400}
.contact .mail{color:var(--ink);font-size:9px;font-weight:400}

.main-nav{left:52px;top:74px;width:744px;height:35px;background:linear-gradient(var(--blue),var(--navy));display:flex;justify-content:space-around;align-items:center;padding:0 6px}
.main-nav a{color:var(--white);font-size:9.5px;font-weight:400}

.hero{left:52px;top:114px;width:744px;height:271px;border:4px solid #c9cbcf;background:linear-gradient(120deg,#16223a 0%,#1f4263 40%,#2b3a4e 70%,#5e6a78 100%)}
.hero-caption{position:absolute;right:0;top:91px;width:368px;height:88px;background:rgba(255,255,255,.86);padding:8px 12px}
.hero-caption h1{font-size:20.5px;font-weight:400;color:var(--purple);margin-bottom:6px}
.hero-caption p{font-size:12.5px;line-height:1.45;color:#222;font-weight:400}
.dots{position:absolute;left:342px;bottom:8px;display:flex;gap:6px}
.dots span{width:9px;height:9px;border-radius:50%;background:var(--white)}
.dots span.on{background:var(--purple)}

.section-title{left:0;width:848px;top:412px;text-align:center;font-size:17px;font-weight:400;color:var(--blue)}

.services{left:52px;top:451px;width:744px;display:flex;justify-content:space-between}
.service{width:172px;height:237px;background:var(--card);border:1px solid #eceef0}
.service .shot{height:105px}
.service h3{font-size:13.5px;font-weight:400;color:var(--purple);padding:9px 12px 6px;line-height:1.3}
.service p{font-size:8.4px;line-height:1.55;padding:0 12px}
.service .more{display:block;font-size:7.6px;padding:10px 12px;font-weight:400}

.rule{left:52px;width:744px;height:1px;background:var(--rule)}
.vrule{left:424px;width:1px;background:var(--rule)}

h2.block-title{font-size:15.5px;font-weight:400;color:var(--ink)}
.welcome{left:53px;top:736px;width:355px}
.welcome p{font-size:8.8px;line-height:1.85;margin-top:10px}
.btn{display:inline-block;margin-top:12px;background:var(--purple);color:var(--white);font-size:9px;padding:7px 15px;font-weight:400}

.news{left:443px;top:736px;width:353px}
.news-item{display:flex;gap:14px;padding:12px 0 12px 2px;border-bottom:1px solid var(--rule)}
.news-item:last-child{border-bottom:none}
.news-item .thumb{width:52px;height:50px;flex:none}
.news-item .date{font-size:10px;color:var(--purple);font-weight:400;margin-bottom:3px}
.news-item p{font-size:8.2px;line-height:1.6}

.team{left:53px;top:941px}
.team-row{display:flex;gap:15px;margin-top:9px;margin-left:-1px}
.member{width:108px;height:135px}

.blog{left:443px;top:941px;width:353px}
.post{padding:8px 2px 9px;border-bottom:1px solid var(--rule)}
.post:last-child{border-bottom:none}
.post h4{font-size:10.5px;font-weight:400;color:var(--purple);margin-bottom:3px}
.post p{font-size:8.7px;line-height:1.55}

.footer{left:0;top:1123px;width:848px;height:77px;background:var(--blue);color:var(--white);text-align:center}
.footer-nav{display:flex;justify-content:center;gap:31px;padding-top:23px}
.footer-nav a{color:var(--white);font-size:8.8px}
.footer small{display:block;margin-top:12px;font-size:8.4px}
</style>
</head>
<body>

<header>
  <div class="abs brand">
    <span class="brand-name">TR Solutions</span>
  </div>
  <div class="abs contact">
    <div><span class="label">Call Us:</span> <span class="phone">+61-4-55501234</span></div>
    <div><span class="label">Email:</span> <span class="mail">office@tr-solutions.example</span></div>
  </div>
  <nav class="abs main-nav">
    <a>HOME</a><a>ABOUT US</a><a>OUR SERVICES</a><a>CASE STUDIES</a><a>LATEST NEWS</a><a>CAREERS</a><a>BLOG</a><a>OUR TEAM</a><a>CONTACT US</a>
  </nav>
</header>

<section class="abs hero" role="img" aria-label="Businessman touching a glowing network of connected nodes">
  <div class="hero-caption">
    <h1>We Are a Programming Company..</h1>
    <p>We Specialise in business finance solutions, Office Suite automation and programming and data analysis.</p>
  </div>
  <div class="dots"><span class="on"></span><span></span><span></span><span></span></div>
</section>

<h2 class="abs section-title">WHAT WE DO</h2>

<section class="abs services">
  <article class="service">
    <div class="shot" role="img" aria-label="Colleagues reviewing documents at a desk" style="background:linear-gradient(135deg,#8fa8c4,#d9dfe6 60%,#7d8fa6)"></div>
    <h3>Business Finance Solutions</h3>
    <p>Lorem ipsum dolor sit amet, consectetur adipisicing eitseo eiusmod tempor incididunt ut labore et dolore magna aliqua...</p>
    <a class="more">READ MORE ››</a>
  </article>
  <article class="service">
    <div class="shot" role="img" aria-label="Smiling office worker at a laptop" style="background:linear-gradient(135deg,#eef0f2,#b9c9dc 60%,#e6e2dc)"></div>
    <h3>Office Suite Automation</h3>
    <p>Lorem ipsum dolor sit amet, consectetur adipisicing eitseo eiusmod tempor incididunt ut labore et dolore magna aliqua...</p>
    <a class="more">READ MORE ››</a>
  </article>
  <article class="service">
    <div class="shot" role="img" aria-label="Program code on a blue screen" style="background:linear-gradient(135deg,#0a2a8c,#1c63d6 55%,#0b2a6e)"></div>
    <h3>Programming</h3>
    <p>Lorem ipsum dolor sit amet, consectetur adipisicing eitseo eiusmod tempor incididunt ut labore et dolore magna aliqua...</p>
    <a class="more">READ MORE ››</a>
  </article>
  <article class="service">
    <div class="shot" role="img" aria-label="Engineers working beside server racks" style="background:linear-gradient(135deg,#c9cfd6,#5a6f63 55%,#25323a)"></div>
    <h3>Data Analysis</h3>
    <p>Lorem ipsum dolor sit amet, consectetur adipisicing eitseo eiusmod tempor incididunt ut labore et dolore magna aliqua...</p>
    <a class="more">READ MORE ››</a>
  </article>
</section>

<div class="abs rule" style="top:714px"></div>
<div class="abs vrule" style="top:736px;height:162px"></div>

<section class="abs welcome">
  <h2 class="block-title">Welcome to Our Company Website</h2>
  <p>Aliquam molestie, mi et imperdiet euismod, dui purus auctor tellus, et interdum lacus lectus et ante. Sed accumsan sollicitudin sapien, sit amet adipiscing turpis gravida ac. In congue, neque ac lobortis volutpat, libero mauris varius mi, vitae suscipit ipsum ligula vitae risus. Duis aliquam nibh a dui iaculis viverra id a velit. Vivamus egestas risus in magna varius commodo. Sed semper viverra egestas. Etiam pretium porttitor lectus, vel ornare neque porta volutpat.</p>
  <a class="btn">Read More ››</a>
</section>

<section class="abs news">
  <h2 class="block-title">Latest News</h2>
  <div class="news-item">
    <div class="thumb" role="img" aria-label="Technician in a server room" style="background:linear-gradient(135deg,#3a4a5c,#9aa8b8)"></div>
    <div><div class="date">Sep24, 2014</div><p>Aliquam molestie, mi et imperdiet euismod, dui purus auctor tellus, et interdum lacus lectus et ante. Sed accumsan sollicitudin sapien, sit amet adipiscing turpis gravida ac...<a>Read More ››</a></p></div>
  </div>
  <div class="news-item">
    <div class="thumb" role="img" aria-label="Businessman with glowing digital screen" style="background:linear-gradient(135deg,#0e2440,#3c7fb8)"></div>
    <div><div class="date">Sep24, 2014</div><p>Aliquam molestie, mi et imperdiet euismod, dui purus auctor tellus, et interdum lacus lectus et ante. Sed accumsan sollicitudin sapien, sit amet adipiscing turpis gravida ac...<a>Read More ››</a></p></div>
  </div>
</section>

<div class="abs rule" style="top:922px"></div>
<div class="abs vrule" style="top:942px;height:162px"></div>

<section class="abs team">
  <h2 class="block-title">Our Team</h2>
  <div class="team-row">
    <div class="member" role="img" aria-label="Portrait of a team member" style="background:linear-gradient(160deg,#e9e6e2,#8c7a6c 70%,#2d2a2a)"></div>
    <div class="member" role="img" aria-label="Portrait of a team member" style="background:linear-gradient(160deg,#ecebe9,#b9b2ab 60%,#cfd4dc)"></div>
    <div class="member" role="img" aria-label="Portrait of a team member" style="background:linear-gradient(160deg,#d9d3cd,#b58a62 60%,#3a2a24)"></div>
  </div>
</section>

<section class="abs blog">
  <h2 class="block-title">Blog Posts</h2>
  <div class="post">
    <h4>Vestibulum ante ipsum primis in faucibus orci luctus et ultrices ..</h4>
    <p>Aliquam molestie, mi et imperdiet euismod, dui purus auctor tellus, et interdum lacus lectus et ante. Sed accumsan sollicitudin sapien, sit amet adipiscing turpis gravida ac...<a>Read More ››</a></p>
  </div>
  <div class="post">
    <h4>Vestibulum ante ipsum primis in faucibus orci luctus et ultrices ..</h4>
    <p>Aliquam molestie, mi et imperdiet euismod, dui purus auctor tellus, et interdum lacus lectus et ante. Sed accumsan sollicitudin sapien, sit amet adipiscing turpis gravida ac...<a>Read More ››</a></p>
  </div>
</section>

<footer class="abs footer">
  <nav class="footer-nav">
    <a>HOME</a><a>ABOUT US</a><a>OUR SERVICES</a><a>CASE STUDIES</a><a>LATEST NEWS</a><a>CAREERS</a><a>BLOG</a><a>OUR TEAM</a><a>CONTACT US</a>
  </nav>
  <small>Copyright © 2014. Company Name. All Right Reserved</small>
</footer>

</body>
</html>
```